TA BRAMLEY BUSINESS CARD DESIGN PROJECT

We need to utilize our logo that was expertly created on PixelHarbor and now need to match this with a business card design.

```html
<!DOCTYPE html>
<html lang="en">
<head>
<meta charset="utf-8">
<title>TA Bramley – Business Card</title>
<link rel="stylesheet" href="https://fonts.googleapis.com/css2?family=Montserrat:wght@400;500;700&family=Open+Sans:wght@400&display=swap">
<style>
  :root {
    --backdrop: #e4e4e2;
    --card-white: #ffffff;
    --card-black: #181818;
    --brand-blue: #0f56ad;
    --text-dark: #1c1c1c;
    --text-light: #f2f2f2;
  }
  * { margin: 0; padding: 0; box-sizing: border-box; }
  html, body { width: 1200px; height: 801px; overflow: hidden; }
  body {
    background: var(--backdrop);
    position: relative;
    font-family: "Open Sans", Arial, sans-serif;
  }
  .card {
    position: absolute;
    top: 260px;
    width: 490px;
    height: 280px;
    overflow: hidden;
    box-shadow: 0 6px 18px rgba(0,0,0,0.18);
  }
  .card-front { left: 80px; background: var(--card-white); }
  .card-back { left: 630px; background: var(--card-black); display: flex; align-items: center; justify-content: center; }

  .front-shapes { position: absolute; inset: 0; }

  .brand-name {
    font-family: "Montserrat", Arial, sans-serif;
    font-weight: 700;
    color: var(--brand-blue);
    letter-spacing: 0.12em;
    line-height: 1;
  }
  .card-front .brand-name {
    position: absolute;
    left: 28px;
    top: 70px;
    font-size: 26px;
    display: flex;
    align-items: center;
    gap: 10px;
  }
  .brand-mark {
    width: 18px; height: 18px;
    background: var(--brand-blue);
  }
  .card-back .brand-name { font-size: 46px; }

  .holder {
    position: absolute;
    right: 44px;
    top: 34px;
    text-align: right;
  }
  .holder-name {
    font-family: "Montserrat", Arial, sans-serif;
    font-weight: 700;
    font-size: 17px;
    color: var(--brand-blue);
    letter-spacing: 0.02em;
  }
  .holder-role {
    font-family: "Montserrat", Arial, sans-serif;
    font-weight: 500;
    font-size: 12px;
    color: var(--text-dark);
    margin-top: 1px;
  }
  .accent-bar {
    position: absolute;
    right: 0; top: 36px;
    width: 36px; height: 14px;
    background: var(--brand-blue);
  }

  .contact-list {
    position: absolute;
    left: 58px;
    top: 192px;
    list-style: none;
    color: var(--text-light);
    font-size: 11.5px;
    line-height: 17px;
  }
  .contact-list li { display: flex; align-items: center; gap: 8px; }
  .contact-list svg { width: 10px; height: 10px; fill: var(--brand-blue); flex: none; }

  .address {
    position: absolute;
    right: 22px;
    top: 150px;
    text-align: right;
    color: var(--text-light);
    font-size: 11.5px;
    line-height: 16px;
  }
</style>
</head>
<body>

  <section class="card card-front">
    <svg class="front-shapes" viewBox="0 0 490 280" preserveAspectRatio="none" aria-hidden="true">
      <path d="M0 172 C 150 150, 320 122, 490 110 L 490 280 L 0 280 Z" fill="var(--card-black)"/>
      <path d="M0 166 C 150 140, 320 106, 490 92 L 490 103 C 320 116, 150 146, 0 168 Z" fill="var(--brand-blue)"/>
    </svg>

    <div class="brand-name"><span class="brand-mark"></span>TA BRAMLEY</div>

    <div class="holder">
      <div class="holder-name">COLIN HART</div>
      <div class="holder-role">Managing Director</div>
    </div>
    <div class="accent-bar"></div>

    <ul class="contact-list">
      <li><svg viewBox="0 0 10 10"><path d="M2 0.5 L4 2.5 L3 3.8 Q4.2 6 6.2 7 L7.5 6 L9.5 8 L8 9.5 Q3 9 0.5 2 Z"/></svg>2233333333</li>
      <li><svg viewBox="0 0 10 10"><path d="M2.5 0 H7.5 V10 H2.5 Z M3.4 1 V8 H6.6 V1 Z"/></svg>00000000000</li>
      <li><svg viewBox="0 0 10 10"><path d="M0 2 H10 V8 H0 Z M0.8 2.6 L5 5.6 L9.2 2.6 V3.4 L5 6.4 L0.8 3.4 Z" fill-rule="evenodd"/></svg>info@tabramley.com</li>
      <li><svg viewBox="0 0 10 10"><circle cx="5" cy="5" r="4.6"/></svg>www.yourwebsite.com</li>
    </ul>

    <div class="address">Your address, City<br>State, Zip 1234</div>
  </section>

  <section class="card card-back">
    <div class="brand-name">TA BRAMLEY</div>
  </section>

</body>
</html>
```